Professional Engineering Web Design

Project Brief: Website Redesign for Mechanical Design Consultancy
Project Overview
I want to update and improve my current website to create a more professional, modern, and high-credibility online presence for my mechanical design consultancy.

Current site: https://valtorix.design/

The new website must communicate expertise, precision, and trust—matching the standard of top engineering and product design agencies.

Reference Websites (Style + Structure Inspiration)
These represent the quality, cleanliness, and professionalism I want to achieve:

https://plinthwaredesign.com/
https://www.sorvane.com/
https://bramlow-uk.com/
Brand Look
Professional, modern, engineering-focused aesthetic
Clean layouts and strong typography
High-quality imagery conveying precision, innovation, and mechanical expertise
Colour scheme and styling must follow my existing logo (attached in project)
Platform Requirements
The website must be built on WordPress
Should use a clean, flexible theme or modern page builder (Elementor, Gutenberg, Bricks, or similar)
Avoid overly complex custom coding so I can easily edit content later
Final deliverable must allow me to manage and update content without developer assistance
Functionality
Fast-loading, lightweight, and smooth user experience
Clean animations and transitions similar to the reference sites
Fully mobile responsive
Clear navigation and strong visual hierarchy
Contact forms optimised for lead generation
Optional: subtle scroll effects, case study sliders, icon animations, etc.
SEO Aspirations
Developer should recommend and implement a modern SEO strategy
Proper on-page SEO setup (titles, meta, schema, alt tags, heading structure)
Optimised site architecture for ranking and crawling
Aim: Generate leads through improved visibility and keyword targeting
Optional but useful: Google Analytics, Google Search Console setup
User Journeys
(Recommended structure)

The site should be crafted around clear, intuitive journeys for each type of visitor:

Potential new clients
Quickly understand what services I offer
View examples of past work / case studies
See credibility indicators (process, expertise, industries served)
Easily contact me or request a project discussion
Returning clients
Access updated portfolio items
Find contact details or book follow-up work easily
General visitors discovering through SEO
Be guided to core service areas
Understand my value proposition quickly
Be invited to learn more or make contact
The developer should design the structure to support these journeys smoothly.

Maintenance Expectations
Website will be maintained by me, so it should be easy to update using relatively basic WordPress skills
Use modular templates and simple backend structure
Avoid unnecessary plugins
Provide brief handover documentation if required
Hosting Preferences
Site is currently hosted via a family member
Open to discussing moving to a paid, reliable hosting provider if preferable for performance and maintainability
Developer may advise on the best hosting setup for WordPress
Content
Most content can be taken from the existing website
Developer is welcome to suggest improvements to structure, layout, and imagery
Must remain easy for me to edit or add new content later (e.g., new projects)
Deliverables
Fully built WordPress website
Clean, professional, modern design inspired by the reference sites
Mobile-responsive across all devices
SEO-ready structure and optimisations
Transfer of website and admin rights
Any design assets, templates, or documentation used

```html
<!DOCTYPE html>
<html lang="en">
<head>
<meta charset="utf-8">
<title>Valtorix Mechanical Design</title>
<link rel="stylesheet" href="https://fonts.googleapis.com/css2?family=Outfit:wght@300;400;500;600;700&display=swap">
<style>
:root{
  --blue:#3361f0;
  --blue-dark:#2549d6;
  --tint:#eef2fe;
  --ink:#111318;
  --text:#3b3e46;
  --muted:#6d717b;
  --footer:#2b2b2d;
  --white:#ffffff;
  --star:#f5a623;
}
*{box-sizing:border-box;margin:0;padding:0}
html,body{width:1200px;height:4688px;overflow:hidden}
body{font-family:'Outfit',sans-serif;color:var(--text);background:var(--white);position:relative}
.abs{position:absolute}
.btn{position:absolute;display:flex;align-items:center;gap:16px;background:var(--blue);color:var(--white);border-radius:24px;height:42px;padding:0 5px 0 24px;font-size:12px;font-weight:500;letter-spacing:.3px;text-transform:uppercase;white-space:nowrap}
.btn .arrow{width:34px;height:34px;border-radius:50%;background:var(--white);display:flex;align-items:center;justify-content:center}
.btn.light{background:var(--white);color:var(--blue);border:2px solid var(--blue)}
.btn.light .arrow{background:var(--blue)}
.eyebrow{color:var(--blue);font-size:16px;font-weight:500;letter-spacing:.5px}
.heading{color:var(--ink);font-size:33px;font-weight:600;text-transform:uppercase;letter-spacing:-.3px;white-space:nowrap}
.center{left:0;width:1200px;text-align:center}
p{font-size:13.5px;line-height:24px}

/* header */
.topbar{left:540px;top:0;width:660px;height:33px;background:var(--blue);clip-path:polygon(22px 0,100% 0,100% 100%,0 100%);color:var(--white);font-size:12px;display:flex;align-items:center;gap:14px;padding-left:46px}
.topbar .dot{width:13px;height:13px;border-radius:3px;background:var(--white);opacity:.9}
.topbar .pill{display:flex;align-items:center;gap:8px;margin-left:18px}
.topbar .pill i{width:24px;height:24px;border-radius:50%;background:var(--white);display:flex;align-items:center;justify-content:center}
.brand{display:flex;align-items:center;gap:10px}
.brand .mark{width:62px;height:62px;border-radius:50%;background:var(--blue)}
.brand .name{font-size:36px;font-weight:600;color:var(--ink);letter-spacing:5px;line-height:1}
.nav{left:452px;top:66px;display:flex;gap:48px;font-size:12.5px;font-weight:500;color:var(--ink)}

/* hero */
.hero-photo{left:0;top:115px;width:1200px;height:580px;background:linear-gradient(120deg,#2c3a3c 0%,#4a5a52 35%,#5d6a7a 60%,#3a3f48 100%)}
.hero-shade{left:0;top:115px;width:1200px;height:580px;background:rgba(10,20,40,.35)}
.hero-title{top:292px;color:var(--white);font-size:52px;font-weight:600}
.hero-sub{top:366px;color:var(--white);font-size:29px;font-weight:300}

/* intro */
.intro-photo{left:142px;top:770px;width:452px;height:452px;border-radius:50%;background:linear-gradient(150deg,#9a7a6c 0%,#56657f 55%,#2e3545 100%);border-left:4px solid var(--blue);border-bottom:4px solid var(--blue)}
.intro{left:647px;top:808px;width:420px}
.intro p{margin-top:14px}

/* expertise */
.band{left:0;width:1200px;background:var(--tint)}
.card{position:absolute;top:1535px;width:288px;height:232px;background:var(--white);border-radius:10px;box-shadow:0 6px 24px rgba(40,60,120,.08);text-align:center;padding-top:70px}
.card h3{font-size:22px;font-weight:600;color:var(--ink);line-height:27px}
.card p{font-size:12.5px;line-height:23px;margin:16px 18px 0;color:var(--text)}
.card .icon{position:absolute;left:95px;top:-49px;width:98px;height:98px;border-radius:50%;background:var(--blue);display:flex;align-items:center;justify-content:center}
.card.active{background:var(--blue)}
.card.active h3,.card.active p{color:var(--white)}
.card.active .icon{border:4px solid var(--white)}

/* portfolio */
.tile{position:absolute;border-radius:4px;background:linear-gradient(135deg,#ececec,#d5d5d7 60%,#e8e8ea)}

/* about */
.about{left:142px;top:2845px;width:410px}
.about p{margin-top:12px}
.portrait{left:606px;top:2808px;width:448px;height:448px;border-radius:50%;background:linear-gradient(160deg,#9aa0a6,#6e6259 60%,#2d3a5a);border-right:5px solid var(--blue);border-bottom:5px solid var(--blue)}

/* reviews */
.review{position:absolute;top:3529px;width:444px;height:300px;background:var(--white);border-radius:8px;box-shadow:0 6px 30px rgba(30,40,80,.08);padding:34px 36px}
.review .who{display:flex;align-items:center;gap:18px}
.review .avatar{width:66px;height:66px;border-radius:50%;background:#f1d9c8;border:2px solid #e7e9ef}
.review .who b{display:block;font-size:17px;font-weight:500;color:var(--ink)}
.review .who span{font-size:14px;color:var(--muted)}
.review p{margin-top:24px;font-size:13.5px;line-height:25px}
.review .stars{position:absolute;left:36px;bottom:34px;color:var(--star);font-size:16px;letter-spacing:3px}
.review .quote{position:absolute;right:36px;bottom:28px}
.dots{top:3873px;left:566px;display:flex;gap:6px}
.dots i{width:12px;height:12px;border-radius:50%;background:#cfd2da}
.dots i:first-child{background:var(--white);border:2px solid var(--blue)}

/* footer */
.footer{left:0;top:4146px;width:1200px;height:542px;background:var(--footer)}
.cta{left:142px;top:3979px;width:916px;height:324px;border-radius:22px;background:linear-gradient(120deg,#3a66f2,#3059e8);text-align:center;color:var(--white)}
.cta h2{margin-top:92px;font-size:33px;font-weight:600;text-transform:uppercase}
.cta p{margin-top:6px;font-size:15px;line-height:27px;font-weight:300}
.fcol{position:absolute;top:4374px;color:var(--white)}
.fcol h4{font-size:15px;font-weight:600;text-transform:uppercase}
.fcol h4:after{content:"";display:block;width:34px;height:2px;background:var(--white);margin-top:8px}
.fcol ul{list-style:none;margin-top:20px;font-size:12px;line-height:29px}
.fitem{display:flex;gap:12px;margin-top:16px;font-size:11.5px;line-height:17px}
.fitem b{font-weight:600;font-size:12px;display:block}
.social{display:flex;align-items:center;gap:12px;margin-top:10px;font-size:12px}
.social i{width:27px;height:27px;border-radius:50%;border:1.5px solid var(--white);display:block}
.flogo{left:848px;top:4372px;width:220px;text-align:center}
.flogo .mark{width:106px;height:106px;border-radius:50%;background:var(--blue);margin:0 auto}
.flogo .name{margin-top:14px;font-size:44px;font-weight:600;color:var(--white);letter-spacing:6px;line-height:1}
.fline{left:142px;top:4640px;width:916px;height:1px;background:rgba(255,255,255,.15)}
.copy{top:4656px;color:#cfd0d4;font-size:11px}
</style>
</head>
<body>

<!-- Header -->
<div class="abs topbar">
  <span class="dot"></span><span class="dot"></span><span class="dot"></span><span class="dot"></span>
  <span class="pill"><i><svg width="12" height="10" viewBox="0 0 12 10"><rect x="1" y="1" width="10" height="8" rx="1" fill="none" stroke="#3361f0" stroke-width="1.4"/><path d="M1 1l5 4 5-4" fill="none" stroke="#3361f0" stroke-width="1.4"/></svg></i>info@valtorix.design</span>
  <span class="pill"><i><svg width="12" height="12" viewBox="0 0 12 12"><path d="M3 1l2 3-1.3 1.2a7 7 0 003 3L8 7l3 2-1 2c-5 0-9-4-9-9z" fill="#3361f0"/></svg></i>+44 (0) 7700 900418</span>
</div>
<div class="abs brand" style="left:140px;top:29px">
  <span class="mark"></span>
  <span class="name">valtorix</span>
</div>
<nav class="abs nav"><span>HOME</span><span>ABOUT US</span><span>OUR SERVICES</span><span>PORTFOLIO</span></nav>
<div class="btn" style="left:902px;top:53px;padding-left:26px">Contact us <span class="arrow"><svg width="12" height="12"><path d="M3 9l6-6M4 3h5v5" stroke="#3361f0" stroke-width="1.5" fill="none"/></svg></span></div>

<!-- Hero -->
<div class="abs hero-photo" role="img" aria-label="Engineers reviewing a turbine CAD model on a monitor in a modern office"></div>
<div class="abs hero-shade"></div>
<svg class="abs" style="left:0;top:560px" width="1200" height="140" viewBox="0 0 1200 140">
  <path d="M0 40 Q520 190 1200 0 L1200 140 L0 140Z" fill="#ffffff"/>
  <path d="M0 40 Q520 170 1200 0 L1200 30 Q560 170 0 58Z" fill="#3361f0"/>
  <path d="M880 96 Q1050 70 1200 20 L1200 64 Q1040 110 880 96Z" fill="#c9d4fb"/>
</svg>
<h1 class="abs center hero-title">Mechanical CAD Design</h1>
<div class="abs center hero-sub">Cutting Edge Engineering</div>
<div class="btn" style="left:523px;top:426px">Contact us <span class="arrow"><svg width="12" height="12"><path d="M3 9l6-6M4 3h5v5" stroke="#3361f0" stroke-width="1.5" fill="none"/></svg></span></div>

<!-- Intro -->
<div class="abs intro-photo" role="img" aria-label="Engineer working on a 3D CAD model at a desktop workstation"></div>
<section class="abs intro">
  <div class="eyebrow" style="text-transform:uppercase">Who we are</div>
  <h2 class="heading" style="font-size:27px;margin-top:4px">Valtorix Mechanical Design</h2>
  <p style="margin-top:18px">Welcome to Valtorix Mechanical Design. We are a UK based design consultancy offering a comprehensive mechanical and product design service from initial concepts through to full volume production.</p>
  <p>Duis autem vel eum iriure dolor in hendrerit in vulputate velit esse molestie consequat, vel illum dolore eu feugiat nulla facilisis at vero eros et accumsan et iusto odio dignissim qui blandit praesent luptatum zzril delenit augue duis dolore te feugait nulla facilisi tincidunt ut laoreet.</p>
</section>
<div class="btn" style="left:647px;top:1138px">Read more <span class="arrow"><svg width="12" height="12"><path d="M3 9l6-6M4 3h5v5" stroke="#3361f0" stroke-width="1.5" fill="none"/></svg></span></div>

<!-- Expertise -->
<div class="abs band" style="top:1315px;height:544px"></div>
<div class="abs center eyebrow" style="top:1405px">Solutions</div>
<h2 class="abs center heading" style="top:1428px">Our Expertise</h2>
<div class="card" style="left:142px"><span class="icon"><svg width="44" height="44" viewBox="0 0 44 44" fill="none" stroke="#fff" stroke-width="2"><path d="M4 22l10-10 8 4 8-4 10 10-14 12z"/></svg></span><h3>Bespoke<br>Product Design</h3><p>Innovative design from concept through the full development life cycle</p></div>
<div class="card active" style="left:455px"><span class="icon"><svg width="44" height="44" viewBox="0 0 44 44" fill="none" stroke="#fff" stroke-width="2"><rect x="6" y="8" width="32" height="22" rx="2"/><path d="M16 36h12M22 30v6"/></svg></span><h3>3D Modelling and<br>Drawings</h3><p>Innovative design from concept through the full development life cycle</p></div>
<div class="card" style="left:770px"><span class="icon"><svg width="44" height="44" viewBox="0 0 44 44" fill="none" stroke="#fff" stroke-width="2"><path d="M6 38V12l9 7v-7l9 7v-7l9 7V6h5v32z"/></svg></span><h3>Design for<br>Manufacture</h3><p>Innovative design from concept through the full development life cycle</p></div>

<!-- Portfolio -->
<div class="abs center eyebrow" style="top:1947px">Projects</div>
<h2 class="abs center heading" style="top:1970px">Our Portfolio</h2>
<div class="abs center" style="top:2021px;font-size:15px;color:var(--text)">A small selection of our previous projects</div>
<div class="tile" style="left:142px;top:2066px;width:319px;height:483px" role="img" aria-label="Rendered industrial processing machine"></div>
<div class="tile" style="left:475px;top:2063px;width:583px;height:213px" role="img" aria-label="Rendered action camera mounted on a long threaded pole"></div>
<div class="tile" style="left:475px;top:2291px;width:279px;height:258px" role="img" aria-label="Rendered alloy wheel"></div>
<div class="tile" style="left:772px;top:2291px;width:286px;height:258px" role="img" aria-label="Rendered go-kart chassis with seat and steering wheel"></div>
<div class="btn light" style="left:532px;top:2584px">View all <span class="arrow"><svg width="12" height="12"><path d="M3 9l6-6M4 3h5v5" stroke="#fff" stroke-width="1.5" fill="none"/></svg></span></div>

<!-- About -->
<div class="abs band" style="top:2717px;height:634px"></div>
<section class="abs about">
  <div class="eyebrow">About Me</div>
  <h2 class="heading" style="margin-top:2px">Rowan Ellery</h2>
  <p style="margin-top:14px">Rowan Ellery is the Chief Engineer at Valtorix Mechanical Design. He has 11 years experience working as a mechanical design engineer in multiple industries including high performance automotive, consumer products, medical, industrial plus many more. He has worked in multiple roles across a wide range of products.</p>
  <p>Ut wisi enim ad minim veniam, quis nostrud exerci t ullamcorper suscipit lobortis nisl ut aliquip ex ea commodo consequat. Duis autem vel eum iriure dolor in hendrerit.</p>
</section>
<div class="btn" style="left:142px;top:3169px">Tell us about your ideas <span class="arrow"><svg width="12" height="12"><path d="M3 9l6-6M4 3h5v5" stroke="#3361f0" stroke-width="1.5" fill="none"/></svg></span></div>
<div class="abs portrait" role="img" aria-label="Portrait of the chief engineer"></div>

<!-- Reviews -->
<div class="abs center eyebrow" style="top:3441px">Testimonials</div>
<h2 class="abs center heading" style="top:3465px">Customer Reviews</h2>
<article class="review" style="left:142px">
  <div class="who"><span class="avatar" role="img" aria-label="Reviewer avatar"></span><div><b>Dorian Hale</b><span>Design Engineer</span></div></div>
  <p>"Rowan is able to bridge the gap between what management want and what manufacturing can deliver. In the field of Casting his intuition for the process and knowledge of casting technical nuances..."</p>
  <div class="stars">★★★★★</div>
  <svg class="quote" width="46" height="36" viewBox="0 0 46 36" fill="none" stroke="#3361f0" stroke-width="2"><path d="M3 34V16L12 2h4l-6 14h8v18zM26 34V16L35 2h4l-6 14h8v18z"/></svg>
</article>
<article class="review" style="left:614px">
  <div class="who"><span class="avatar" style="background:#e9c6c6" role="img" aria-label="Reviewer avatar"></span><div><b>Nadia Brennick</b><span>Client</span></div></div>
  <p>"5* Rowan was amazing. His communication was excellent, responded very quickly, started working on the project the same day I purchased, and problem solved every little detail with my design. He clearly..."</p>
  <div class="stars">★★★★★</div>
  <svg class="quote" width="46" height="36" viewBox="0 0 46 36" fill="none" stroke="#3361f0" stroke-width="2"><path d="M3 34V16L12 2h4l-6 14h8v18zM26 34V16L35 2h4l-6 14h8v18z"/></svg>
</article>
<div class="abs dots"><i></i><i></i><i></i><i></i></div>

<!-- Footer -->
<div class="abs footer"></div>
<section class="abs cta">
  <h2>Curious what else we do?</h2>
  <p>Duis autem vel eum iriure dolor in hendrerit in vulputate velit esse molestie consequat,<br>vel illum dolore eu feugiat nulla facilisis at vero eros et accumsan.</p>
</section>
<div class="btn light" style="left:532px;top:4175px;border-color:#fff">See here <span class="arrow"><svg width="12" height="12"><path d="M3 9l6-6M4 3h5v5" stroke="#fff" stroke-width="1.5" fill="none"/></svg></span></div>

<div class="fcol" style="left:142px"><h4>Quick Links</h4><ul><li>· Home</li><li>· About Us</li><li>· Our Services</li><li>· Portfolio</li><li>· Contact Us</li></ul></div>
<div class="fcol" style="left:356px"><h4>Contact Details</h4>
  <div class="fitem" style="margin-top:22px"><svg width="12" height="16" viewBox="0 0 12 16"><path d="M6 15s5-6 5-9A5 5 0 001 6c0 3 5 9 5 9z" fill="#fff"/><circle cx="6" cy="6" r="2" fill="#2b2b2d"/></svg><div><b>ADDRESS</b>Quarry Lane, Newport, UK</div></div>
  <div class="fitem"><svg width="12" height="12" viewBox="0 0 12 12"><path d="M3 1l2 3-1.3 1.2a7 7 0 003 3L8 7l3 2-1 2c-5 0-9-4-9-9z" fill="#fff"/></svg><div><b>PHONE</b>+44 (0)7700 900 418</div></div>
  <div class="fitem"><svg width="12" height="10" viewBox="0 0 12 10"><rect x="0" y="0" width="12" height="10" rx="1" fill="#fff"/><path d="M0 1l6 4 6-4" fill="none" stroke="#2b2b2d" stroke-width="1.2"/></svg><div><b>EMAIL</b>info@valtorix.design</div></div>
</div>
<div class="fcol" style="left:653px"><h4>Follow Us</h4>
  <div class="social" style="margin-top:18px"><i style="background:var(--blue);border-color:var(--blue)"></i>Friendloop</div>
  <div class="social"><i></i>Vidstream</div>
  <div class="social"><i></i>Snapwall</div>
  <div class="social"><i></i>Workgrid</div>
</div>
<div class="abs flogo"><div class="mark"></div><div class="name">valtorix</div></div>
<div class="abs fline"></div>
<div class="abs center copy">© 2025 Valtorix Mechanical Design. All Rights Reserved.</div>

</body>
</html>
```